Graphic Design of Business Process

We require an eye-catching, sophisticated design of 2 business processes (attached), that will be used digitally AND for print (to be put on walls in our office).

The basic layout is attached. We require a creative, professional designer to re-design these so that they look appealing but still able to grasp all the information.

We will require vector files and editable project files for final delivery. You may refer to our website (quillharbourworks.com.au) for an indication of our brand.

If you have any questions, please ask.

Thank you.

```html
<!DOCTYPE html>
<html lang="en">
<head>
<meta charset="utf-8">
<title>Sales &gt; Content Funnel</title>
<link href="https://fonts.googleapis.com/css2?family=Rubik:wght@700;900&family=Arimo:wght@400;700&display=swap" rel="stylesheet">
<style>
  :root {
    --red: #e8452f;
    --red-dark: #d2372a;
    --red-light: #ef6a5a;
    --green: #3f8a44;
    --green-dark: #2f7436;
    --green-light: #4d9a50;
    --orange: #f38a35;
    --orange-dark: #e8762a;
    --orange-light: #f7a05a;
    --blue: #1f7dc1;
    --blue-dark: #1569a8;
    --blue-light: #3bb3e6;
    --cone: #2ea7e0;
    --title: #1a6fb0;
    --white: #ffffff;
  }
  html, body { margin: 0; padding: 0; overflow: hidden; background: var(--white); }
  .canvas { width: 1200px; height: 750px; display: block; }
  .title { font-family: "Rubik", sans-serif; font-weight: 700; font-size: 38px; fill: var(--title); }
  .stage-name { font-family: "Rubik", sans-serif; font-weight: 900; font-size: 28px; fill: var(--white); }
  .funnel-head { font-family: "Rubik", sans-serif; font-weight: 900; font-size: 26px; fill: var(--white); }
  .tag { font-family: "Arimo", sans-serif; font-weight: 700; font-size: 15px; }
  .bullet { font-family: "Arimo", sans-serif; font-size: 12.5px; fill: var(--white); }
  .funnel-note { font-family: "Arimo", sans-serif; font-weight: 700; font-size: 12.5px; fill: var(--white); }
  .shadowed { filter: drop-shadow(1px 2px 1px rgba(0,0,0,.35)); }
  .icon { fill: none; stroke: var(--white); stroke-width: 2.4; stroke-linecap: round; stroke-linejoin: round; }
</style>
</head>
<body>
<svg class="canvas" viewBox="0 0 1440 900" xmlns="http://www.w3.org/2000/svg">
  <!-- heading -->
  <text class="title" x="715" y="100" text-anchor="middle">SALES &gt; CONTENT FUNNEL</text>
  <rect x="449" y="104" width="532" height="2.5" fill="var(--title)"/>

  <!-- awareness stage -->
  <g class="stage stage-awareness">
    <polyline points="80,265 80,360 390,360" fill="none" stroke="var(--red)" stroke-width="3"/>
    <polygon points="87,235 355,235 412,352 87,352" fill="var(--red)"/>
    <text class="stage-name shadowed" x="103" y="275">AWARENESS</text>
    <rect x="100" y="280" width="218" height="20" fill="var(--white)"/>
    <text class="tag" x="106" y="296" fill="var(--red)">IDENTIFY PROBLEM/NEED</text>
    <circle cx="107" cy="313" r="3.5" fill="var(--white)"/>
    <text class="bullet" x="115" y="317">ASPIRATIONAL</text>
    <circle cx="107" cy="330" r="3.5" fill="var(--white)"/>
    <text class="bullet" x="115" y="334">MARKET THE OUTCOME NOT PRODUCT</text>
  </g>

  <!-- consideration stage -->
  <g class="stage stage-consideration">
    <polyline points="118,405 118,500 465,500" fill="none" stroke="var(--green)" stroke-width="3"/>
    <polygon points="125,374 430,374 488,492 125,492" fill="var(--green)"/>
    <text class="stage-name shadowed" x="141" y="408">CONSIDERATION</text>
    <rect x="141" y="413" width="221" height="20" fill="var(--white)"/>
    <text class="tag" x="146" y="429" fill="var(--green)">EVALUATE ALTERNATIVES</text>
    <circle cx="146" cy="444" r="3.5" fill="var(--white)"/>
    <text class="bullet" x="155" y="448">WHY IS THIS SOLUTION BETTER THAN OTHERS</text>
    <circle cx="146" cy="462" r="3.5" fill="var(--white)"/>
    <text class="bullet" x="155" y="466">HOW LONG IS THIS PROVIDER GOING TO</text>
    <text class="bullet" x="155" y="482">SOLVE MY NEED</text>
  </g>

  <!-- action stage -->
  <g class="stage stage-action">
    <polyline points="170,538 170,632 343,632" fill="none" stroke="var(--orange)" stroke-width="3"/>
    <polygon points="178,507 510,507 565,625 178,625" fill="var(--orange)"/>
    <text class="stage-name shadowed" x="197" y="552">ACTION/DECISION</text>
    <rect x="195" y="560" width="178" height="20" fill="var(--white)"/>
    <text class="tag" x="202" y="576" fill="var(--orange)">PRESENT AN OFFER</text>
    <circle cx="200" cy="596" r="3.5" fill="var(--white)"/>
    <text class="bullet" x="209" y="600">WHICH PROVIDER?</text>
  </g>

  <!-- funnel -->
  <g class="funnel">
    <path d="M585,640 Q646,628 710,640 L648,758 Z" fill="var(--cone)"/>
    <path d="M615,645 L680,645 L648,758 Z" fill="var(--blue-light)" opacity=".6"/>

    <path d="M508,505 Q646,490 785,505 L722,625 Q646,650 570,625 Z" fill="var(--orange)"/>
    <path d="M545,515 Q646,505 750,515 L705,625 Q646,640 590,625 Z" fill="var(--orange-light)" opacity=".45"/>
    <path d="M508,505 Q646,485 785,505 Q646,525 508,505 Z" fill="var(--orange-dark)"/>

    <path d="M430,374 Q646,355 862,374 L800,492 Q646,515 490,492 Z" fill="var(--green)"/>
    <path d="M475,385 Q646,372 820,385 L775,495 Q646,510 515,495 Z" fill="var(--green-light)" opacity=".55"/>
    <path d="M430,374 Q646,352 862,374 Q646,392 430,374 Z" fill="var(--green-dark)"/>

    <path d="M355,235 Q646,200 937,235 L877,352 Q646,385 420,352 Z" fill="var(--red)"/>
    <path d="M485,250 Q646,236 810,250 L770,352 Q646,372 520,354 Z" fill="var(--red-dark)" opacity=".35"/>
    <path d="M355,235 Q646,198 937,235 Q646,262 355,235 Z" fill="var(--red-dark)"/>

    <text class="funnel-head shadowed" x="650" y="305" text-anchor="middle">PROBLEM &amp; SOLUTION</text>
    <polygon points="517,312 785,312 770,348 530,348" fill="var(--red-light)"/>
    <text class="funnel-note" x="650" y="326" text-anchor="middle">SUBJECTS SHOWING SYMPTOMS</text>
    <text class="funnel-note" x="650" y="343" text-anchor="middle">OF PROBLEM</text>

    <text class="funnel-head shadowed" x="650" y="428" text-anchor="middle">PROVIDERS &amp; TYPES</text>
    <text class="funnel-head shadowed" x="650" y="455" text-anchor="middle">OF SOLUTION</text>
    <text class="funnel-note" x="650" y="479" text-anchor="middle">SUBJECT GIVES NAME</text>
    <text class="funnel-note" x="650" y="495" text-anchor="middle">TO PROBLEM</text>

    <text class="funnel-head shadowed" x="650" y="573" text-anchor="middle">CONVERT &amp;</text>
    <text class="funnel-head shadowed" x="648" y="600" text-anchor="middle">RETAIN</text>
  </g>

  <!-- feedback loop -->
  <g class="loop">
    <polyline points="1210,383 1210,300 965,300" fill="none" stroke="var(--red)" stroke-width="7"/>
    <polygon points="905,302 967,285 967,319" fill="var(--red)"/>
    <polyline points="1060,439 892,439" fill="none" stroke="var(--green)" stroke-width="7"/>
    <polygon points="830,439 892,422 892,456" fill="var(--green)"/>
    <polyline points="1210,495 1210,575 815,575" fill="none" stroke="var(--orange)" stroke-width="7"/>
    <polygon points="755,575 817,558 817,592" fill="var(--orange)"/>

    <g class="badge badge-idea">
      <circle cx="1073" cy="306" r="43" fill="var(--red-dark)"/>
      <circle cx="1073" cy="306" r="36" fill="var(--red)"/>
      <path class="icon" d="M1065,318 C1065,311 1061,309 1061,302 A12,12 0 0 1 1085,302 C1085,309 1081,311 1081,318 Z M1066,322 H1080 M1068,326 H1078 M1073,284 V280 M1058,290 L1055,287 M1088,290 L1091,287"/>
    </g>
    <g class="badge badge-ideas">
      <circle cx="985" cy="439" r="43" fill="var(--green-dark)"/>
      <circle cx="985" cy="439" r="36" fill="var(--green)"/>
      <path class="icon" d="M968,440 C968,435 964,433 964,428 A8,8 0 0 1 980,428 C980,433 976,435 976,440 Z M969,444 H975 M990,453 C990,448 986,446 986,441 A8,8 0 0 1 1002,441 C1002,446 998,448 998,453 Z M991,457 H997 M972,414 V411 M994,427 V424"/>
    </g>
    <g class="badge badge-cycle">
      <circle cx="917" cy="575" r="43" fill="var(--orange-dark)"/>
      <circle cx="917" cy="575" r="36" fill="var(--orange)"/>
      <path class="icon" d="M901,578 A16,16 0 0 1 928,563 M928,563 L929,555 M928,563 L920,564 M933,572 A16,16 0 0 1 906,587 M906,587 L905,595 M906,587 L914,586"/>
    </g>

    <g class="referral">
      <rect x="1278" y="405" width="80" height="112" fill="var(--blue-dark)"/>
      <polyline points="1363,412 1363,524 1280,524" fill="none" stroke="var(--blue)" stroke-width="3"/>
      <polygon points="1278,495 1306,495 1278,517" fill="var(--blue-light)"/>
      <polygon points="1055,439 1118,383 1118,495" fill="var(--blue-dark)"/>
      <rect x="1118" y="383" width="188" height="112" fill="var(--blue)"/>
      <text class="funnel-head shadowed" x="1213" y="432" text-anchor="middle" font-size="28">WOM &amp;</text>
      <text class="funnel-head shadowed" x="1213" y="461" text-anchor="middle" font-size="28">REFERRAL</text>
    </g>
  </g>
</svg>
</body>
</html>
```